WordPress Design (redesign) and Coding for Funeral Consulting Services & mobile app

I need an attractive SEO friendly WordPress design.

Incorporating all of the latest design standards in a graceful and appealing way. I'd like to see CTA's for for funeral consulting services. People should be able to purchase my consulting services directly from the website so I'd like to see nice buttons.

Funeral Consulting Services are the main topic for this website.

I also have an iOS app called Velomarque in the iOS Appvault Shelf. I want buttons and CTAs so that users can download the app right to their iOS device(s). Make this a secondary focus.

I want more of a mobile focus as that is where I expect the most traffic. Mobile users like to act quickly and they also like to scroll if their interest is captured so I want the design to reflect that.

End to end design
Large Creative Typography for increased mobile searchers.
attractive CTA’s
RGB Vivid / Bright Colors that match our logo
A menu that is easy to find and use on mobile devices
button(s) for iOS app download.

the current website is www.velomarque-example.com This website was a placeholder.
Updates

I'd need users to fill out a survey so that I may collect information from them to better provide service to them.

reference websites: Quillvant.com & Torbex.com for website design inspiratioin. reference Harnwick.com for blog

Target Market(s)

18-35 year old mobile users

Industry/Entity Type

Consulting

Coding

Coded - Design and coding required

Font styles to use
Sans Serif

Colors
fbee3d
000000
ffffff
cbcbcb
fefdec

Requirements
Must have
• iOS app logo and iOS app logo colors should have its own area/page
• CTA's for consulting services and app download. Main topic
• reviews (testimonials)
• Video area
• end to end design
• creative typography
Nice to have
• a beautiful blog page that blends well with the design
Should not have
• Any imagery related to funerals or burials.

```html
<!DOCTYPE html>
<html lang="en">
<head>
<meta charset="utf-8">
<title>Velomarque — Funeral Consulting</title>
<link rel="stylesheet" href="https://fonts.googleapis.com/css2?family=PT+Serif:ital,wght@0,400;0,700;1,400;1,700&display=swap">
<style>
:root{
  --yellow:#f2c315;
  --gold:#b8862b;
  --gold-dark:#a7791f;
  --ink:#2b2b2b;
  --muted:#6d6d6d;
  --white:#ffffff;
  --grey:#d7d7d7;
  --navy:#1c3763;
  --navy-deep:#132849;
  --footer:#ffffff;
  --play-bg:rgba(20,20,20,.55);
}
*{box-sizing:border-box;margin:0;padding:0}
html,body{width:1200px;height:3947px;overflow:hidden}
body{font-family:"PT Serif",Georgia,serif;color:var(--ink);background:var(--white);position:relative}
a{color:inherit;text-decoration:none}
.section{position:absolute;left:0;width:1200px}

/* header */
.site-header{top:0;height:105px;background:var(--white)}
.brand{position:absolute;left:96px;top:30px;font-size:40px;font-weight:700;color:#111}
.social-top{position:absolute;right:100px;top:24px;display:flex;gap:22px}
.social-top span{width:10px;height:10px;border-radius:50%;background:#333}
.main-nav{position:absolute;right:100px;top:64px;display:flex;gap:50px;font-size:13px;font-weight:700;color:#333;letter-spacing:.3px}

/* hero */
.hero{top:105px;height:600px}
.hero-photo{position:absolute;inset:0;background:linear-gradient(100deg,#9b8f7a 0%,#7e7363 35%,#55514b 60%,#2f2e2c 100%)}
.hero-title{position:absolute;left:100px;top:168px;font-size:68px;font-style:italic;font-weight:700;color:var(--white)}
.hero-sub{position:absolute;left:100px;top:262px;width:360px;font-size:23px;font-style:italic;color:var(--white);line-height:1.3}
.hero-wave{position:absolute;left:0;bottom:0;width:1200px;height:110px}

/* about */
.about{top:700px;height:388px;background:var(--yellow)}
.about h2{position:absolute;left:100px;top:50px;font-size:30px;font-weight:700;color:#2a2a2a}
.about p{position:absolute;left:100px;top:112px;width:440px;font-size:12.5px;line-height:1.75;color:#6b5310}
.btn{display:inline-flex;align-items:center;justify-content:center;height:38px;padding:0 24px;border-radius:20px;font-size:12px;font-weight:700;letter-spacing:.3px;border:1.5px solid transparent}
.btn-outline-dark{border-color:#5a4510;color:#2a2a2a}
.about .btn{position:absolute;left:100px;top:285px}
.about-photo{position:absolute;left:656px;top:60px;width:446px;height:266px;border-radius:0 36px 0 36px;background:linear-gradient(120deg,#d9d4cc,#8b8e96 55%,#3d3f44)}

/* videos */
.videos{top:1088px;height:944px;background:var(--white)}
.videos h2{position:absolute;top:50px;width:100%;text-align:center;font-size:30px;font-weight:700;color:#333}
.video{position:absolute;width:452px;box-shadow:0 6px 14px rgba(0,0,0,.3)}
.video .thumb{width:100%;height:100%}
.play{position:absolute;left:50%;top:50%;width:52px;height:52px;margin:-26px 0 0 -26px}
.v1{left:137px;top:134px;height:268px}
.v2{left:607px;top:160px;height:268px}
.v3{left:137px;top:422px;height:268px}
.v4{left:607px;top:448px;height:268px}
.v1 .thumb{background:linear-gradient(120deg,#dcd6cf,#b9aea3 50%,#8f8379)}
.v2 .thumb{background:linear-gradient(120deg,#c9c1b5,#a59a8c 50%,#e3e0dc)}
.v3 .thumb{background:linear-gradient(120deg,#8a5a35,#c28b58 50%,#e6ddd5)}
.v4 .thumb{background:linear-gradient(120deg,#bcb6ab,#9cab93 50%,#6f7a63)}
.videos-caption{position:absolute;top:760px;width:100%;text-align:center;font-size:12.5px;line-height:1.8;color:#777}
.btn-outline-gold{border-color:var(--gold);color:var(--gold)}
.videos .btn{position:absolute;left:508px;top:835px;width:184px}

/* consult band */
.consult{top:2032px;height:312px;display:flex}
.consult-col{width:600px;height:100%;position:relative;padding:60px 0 0 100px}
.consult-left{background:var(--gold)}
.consult-right{background:var(--yellow);padding-left:50px}
.consult-col p{width:430px;font-size:12.5px;line-height:1.8;color:var(--white)}
.consult-right p{color:#6b5310}
.btn-outline-light{border-color:var(--white);color:var(--white)}
.consult-col .btn{position:absolute;bottom:60px}
.consult-right .btn{border-color:#5a4510;color:#2a2a2a}

/* app band */
.app{top:2344px;height:240px;background:var(--grey)}
.app-photo{position:absolute;left:0;top:0;width:700px;height:240px;background:linear-gradient(100deg,#3a3936,#5e5a53 45%,#7b766f);clip-path:polygon(0 0,592px 0,700px 240px,0 240px)}
.app-photo p{position:absolute;left:100px;top:36px;width:430px;font-size:12.5px;line-height:1.8;color:var(--white)}
.app-photo .btn{position:absolute;left:100px;top:132px}
.app-phone{position:absolute;left:630px;top:48px;width:190px;height:158px;border-radius:14px;background:linear-gradient(160deg,#222 0%,#555 50%,#c9b36b 100%);transform:rotate(-14deg)}
.app-title{position:absolute;left:828px;top:60px;font-size:16px;font-weight:700;color:#2a2a2a}
.btn-gold{background:var(--gold);color:var(--white);gap:8px}
.app .btn-gold{position:absolute;left:884px;top:100px;height:44px;padding:0 20px}

/* blog */
.blog{top:2584px;height:592px;background:var(--white)}
.blog h2{position:absolute;left:96px;top:32px;font-size:30px;font-weight:700;color:#333}
.post{position:absolute;top:116px;width:308px}
.post-img{height:196px;box-shadow:0 4px 10px rgba(0,0,0,.25)}
.post h3{margin-top:24px;font-size:15.5px;font-weight:700;line-height:1.35;color:#222}
.post p{margin-top:12px;font-size:11.5px;line-height:1.75;color:#777}
.post .btn{margin-top:18px;height:36px;padding:0 26px;font-size:11px}
.p1{left:100px}.p2{left:446px}.p3{left:792px}
.p1 .post-img{background:linear-gradient(120deg,#5aa59a,#c8c4bd 50%,#3d3b3a)}
.p2 .post-img{background:linear-gradient(120deg,#e7e4de,#7b95b8 50%,#c8c2b7)}
.p3 .post-img{background:linear-gradient(120deg,#b4aea5,#6c655c 50%,#d7d2cb)}

/* reviews */
.reviews{top:3176px;height:366px;background:radial-gradient(circle at 25% 20%,#3a5c8c 0%,var(--navy) 40%,var(--navy-deep) 100%)}
.reviews h2{position:absolute;top:48px;width:100%;text-align:center;font-size:30px;font-weight:700;color:var(--white);letter-spacing:1px}
.arrows{position:absolute;right:98px;top:88px;display:flex;gap:12px}
.arrows span{width:28px;height:28px;border-radius:50%;background:var(--white)}
.arrows svg{display:block}
.avatar{position:absolute;left:98px;top:150px;width:94px;height:94px;border-radius:50%;border:3px solid var(--white);background:linear-gradient(160deg,#c2ccd6,#5b6f85)}
.review-rule{position:absolute;left:232px;top:150px;width:2px;height:118px;background:rgba(255,255,255,.6)}
.review-text{position:absolute;left:264px;top:150px;width:800px;font-size:12.5px;font-style:italic;line-height:1.75;color:#e1e7f0}
.quote-mark{position:absolute;left:290px;top:250px;font-size:72px;font-weight:700;color:var(--white);line-height:1}
.reviewer{position:absolute;right:180px;top:266px;text-align:left;color:var(--white)}
.reviewer strong{display:block;font-size:18px}
.reviewer span{font-size:12px;font-style:italic;color:#c9d2e0}

/* footer */
.site-footer{top:3542px;height:405px;background:var(--footer)}
.footer-brand{position:absolute;left:100px;top:46px}
.footer-brand .badge{width:150px;height:150px;border-radius:50%;background:var(--yellow)}
.footer-brand .name{margin-top:12px;font-size:18px;font-weight:700;color:#111}
.footer-brand p{margin-top:6px;width:200px;font-size:11.5px;line-height:1.6;color:#555}
.footer-col{position:absolute;top:58px}
.footer-col h4{font-size:18px;font-weight:700;color:#222;letter-spacing:.4px}
.newsletter{left:376px;width:300px}
.newsletter p{margin-top:18px;font-size:11.5px;line-height:1.7;color:#666}
.newsletter .field{margin-top:16px;height:36px;border:1px solid #ccc;padding:0 12px;font-size:11px;color:#999;display:flex;align-items:center;width:290px}
.newsletter .btn-sub{margin-top:20px;display:inline-flex;align-items:center;height:34px;padding:0 30px;background:var(--yellow);font-size:12px;font-weight:700;color:#222}
.contact{left:716px;width:230px}
.contact ul{list-style:none;margin-top:22px}
.contact li{display:flex;gap:14px;font-size:11.5px;line-height:1.6;color:#555;margin-bottom:16px}
.contact svg{flex:none;margin-top:2px}
.links{left:974px}
.links ul{list-style:none;margin-top:20px}
.links li{font-size:11.5px;color:#555;line-height:2}
.links li::before{content:"› ";color:#222}
.footer-social{display:flex;gap:12px;margin-top:18px}
.footer-social span{width:32px;height:32px;border-radius:50%}
.footer-social span:nth-child(1){background:#3b5d9c}
.footer-social span:nth-child(2){background:#2da1e0}
.footer-social span:nth-child(3){background:var(--gold)}
.footer-rule{position:absolute;left:98px;right:98px;top:334px;height:1px;background:#ddd}
.copyright{position:absolute;top:358px;width:100%;text-align:center;font-size:11px;color:#666}
</style>
</head>
<body>

<header class="section site-header">
  <div class="brand">Velomarque</div>
  <div class="social-top" aria-label="Social links"><span></span><span></span><span></span></div>
  <nav class="main-nav">
    <a href="#">HOME</a><a href="#">ABOUT</a><a href="#">BLOG</a><a href="#">APP REVIEWS</a><a href="#">VIDEOS</a><a href="#">CONTACT</a>
  </nav>
</header>

<section class="section hero">
  <div class="hero-photo" role="img" aria-label="Young woman in a knit hat looking down thoughtfully"></div>
  <h1 class="hero-title">Velomarque</h1>
  <p class="hero-sub">At vero eos et accusamus et iusto odio dignissimos ducimus</p>
  <svg class="hero-wave" viewBox="0 0 1200 110" preserveAspectRatio="none">
    <path d="M0 48 C260 110 520 110 760 70 C930 42 1070 20 1200 32 L1200 110 L0 110 Z" fill="var(--yellow)"/>
  </svg>
</section>

<section class="section about">
  <h2>ABOUT VELOMARQUE</h2>
  <p>Funerals are expensive. Having to finance one suddenly can be a burden to many families, especially those that are uninsured or unprepared. Not coincidentally, there is often a windfall of money at this time, in the form of donations, family contributions, and life insurance proceeds. Families tend to consider that money 'going away' funds. The funeral industry wants to pressure you into spending your last dollar on that event.</p>
  <a class="btn btn-outline-dark" href="#">DON'T THROW MONEY AWAY</a>
  <div class="about-photo" role="img" aria-label="Consultant talking with a young man in an office"></div>
</section>

<section class="section videos">
  <h2>OUR VIDEOS</h2>
  <div class="video v1"><div class="thumb" role="img" aria-label="Woman comforting a friend on a sofa"></div><svg class="play" viewBox="0 0 52 52"><circle cx="26" cy="26" r="24" fill="var(--play-bg)" stroke="#fff" stroke-width="2"/><path d="M21 16 L36 26 L21 36 Z" fill="#fff"/></svg></div>
  <div class="video v2"><div class="thumb" role="img" aria-label="Woman speaking during a consultation"></div><svg class="play" viewBox="0 0 52 52"><circle cx="26" cy="26" r="24" fill="var(--play-bg)" stroke="#fff" stroke-width="2"/><path d="M21 16 L36 26 L21 36 Z" fill="#fff"/></svg></div>
  <div class="video v3"><div class="thumb" role="img" aria-label="Couple meeting with an older woman"></div><svg class="play" viewBox="0 0 52 52"><circle cx="26" cy="26" r="24" fill="var(--play-bg)" stroke="#fff" stroke-width="2"/><path d="M21 16 L36 26 L21 36 Z" fill="#fff"/></svg></div>
  <div class="video v4"><div class="thumb" role="img" aria-label="Counsellor taking notes with a client"></div><svg class="play" viewBox="0 0 52 52"><circle cx="26" cy="26" r="24" fill="var(--play-bg)" stroke="#fff" stroke-width="2"/><path d="M21 16 L36 26 L21 36 Z" fill="#fff"/></svg></div>
  <p class="videos-caption">The fact is, life insurance was never intended to be fully used on a fancy funeral,<br>but rather as a hedge against disaster for the survivors.</p>
  <a class="btn btn-outline-gold" href="#">SAVE MONEY NOW</a>
</section>

<section class="section consult">
  <div class="consult-col consult-left">
    <p>A funeral consultant is someone who, on their own, goes out and does all the things related to making funeral arrangements. However we do so with your budget and your ideals in mind. We represent you as your spokesperson and friend during this tough time.</p>
    <a class="btn btn-outline-light" href="#">GET HELP ASAP</a>
  </div>
  <div class="consult-col consult-right">
    <p>The first step in funeral planning, particularly if you find yourself at need, is to get a friend by your side. This should be someone who is somewhat removed from the deceased, so the friend's emotions will not be a factor. It should also be someone whose judgement you trust and, preferably, someone who has been through the arrangement process in the recent past.</p>
    <a class="btn" href="#">SAVE MONEY TODAY</a>
  </div>
</section>

<section class="section app">
  <div class="app-photo" role="img" aria-label="Muted photo of a family gathered together">
    <p>In a survey of several thousand funeral directors, in response to the question 'Why would you say funerals cost so much?', over 45% replied: 'Emotional overspending by the family'.</p>
    <a class="btn btn-outline-light" href="#">GET HELP NOW</a>
  </div>
  <div class="app-phone" role="img" aria-label="Smartphone showing the Velomarque app home screen"></div>
  <div class="app-title">Velomarque in the Appvault Shelf</div>
  <a class="btn btn-gold" href="#"><svg width="12" height="12" viewBox="0 0 12 12"><path d="M6 1 V8 M3 5 L6 8 L9 5 M1 11 H11" stroke="#fff" stroke-width="1.6" fill="none"/></svg>DOWNLOAD APP NOW</a>
</section>

<section class="section blog">
  <h2>BLOG POST</h2>
  <article class="post p1">
    <div class="post-img" role="img" aria-label="Two people talking at a table"></div>
    <h3>Lorem Ipsum is that it has a more-or-less normal distribution</h3>
    <p>Sed ut perspiciatis unde omnis iste natus error voluptatem accusantium doloremque laudantium, totam rem aperiam, eaque ipsa quae ab illo inventore veritatis et.</p>
    <a class="btn btn-gold" href="#">READ MORE &gt;&gt;</a>
  </article>
  <article class="post p2">
    <div class="post-img" role="img" aria-label="Man sitting on a couch with head in hands"></div>
    <h3>Contrary to popular belief, Lorem Ipsum is not simply random</h3>
    <p>Quis autem vel eum iure reprehenderit qui in ea voluptate velit esse quam nihil molestiae consequatur, vel illum qui dolorem eum fugiat quo voluptas nulla pariatur.</p>
    <a class="btn btn-gold" href="#">READ MORE &gt;&gt;</a>
  </article>
  <article class="post p3">
    <div class="post-img" role="img" aria-label="Older couple seated in conversation"></div>
    <h3>The standard chunk of Lorem Ipsum used since the 1500s</h3>
    <p>Nor again is there anyone who loves or pursues desires to obtain itself, because it is pain, but because occasionally circumstances occur in which toil and pain can procure.</p>
    <a class="btn btn-gold" href="#">READ MORE &gt;&gt;</a>
  </article>
</section>

<section class="section reviews">
  <h2>REVIEWS</h2>
  <div class="arrows">
    <span><svg width="28" height="28" viewBox="0 0 28 28"><path d="M16 9 L11 14 L16 19" stroke="#1c3763" stroke-width="2" fill="none"/></svg></span>
    <span><svg width="28" height="28" viewBox="0 0 28 28"><path d="M12 9 L17 14 L12 19" stroke="#1c3763" stroke-width="2" fill="none"/></svg></span>
  </div>
  <div class="avatar" role="img" aria-label="Reviewer portrait"></div>
  <div class="review-rule"></div>
  <p class="review-text">Lorem ipsum dolor sit amet, consectetur adipiscing elit, sed do eiusmod tempor incididunt ut labore et dolore magna aliqua. Ut enim ad minim veniam, quis nostrud exercitation ullamco laboris nisi ut aliquip ex ea commodo consequat. Duis aute irure dolor in reprehenderit in voluptate velit esse cillum.</p>
  <div class="quote-mark">”</div>
  <div class="reviewer"><strong>- Person Name</strong><span>- Location</span></div>
</section>

<footer class="section site-footer">
  <div class="footer-brand">
    <div class="badge"></div>
    <div class="name">Velomarque</div>
    <p>At vero eos et accusamus et iusto odio dignissimos ducimus qui blanditiis</p>
  </div>
  <div class="footer-col newsletter">
    <h4>SIGNUP FOR NEWSLETTER</h4>
    <p>On the other hand, we denounce with righteous indignation and dislike men who are so beguiled</p>
    <div class="field">Enter Your Email</div>
    <a class="btn-sub" href="#">SUBSCRIBE</a>
  </div>
  <div class="footer-col contact">
    <h4>CONTACT US</h4>
    <ul>
      <li><svg width="12" height="14" viewBox="0 0 12 14"><path d="M6 13 C2 8 1 6 1 5 A5 5 0 0 1 11 5 C11 6 10 8 6 13 Z" fill="#555"/><circle cx="6" cy="5" r="1.8" fill="#fff"/></svg><span>48 Larkmoor Lane, Fenbridge,<br>CA 90411 USA.</span></li>
      <li><svg width="12" height="12" viewBox="0 0 12 12"><path d="M2 1 L4.5 1 L5.5 4 L4 5 C5 7 6 8 7 8.5 L8 7 L11 8 L11 10.5 C11 11 10 11.5 9 11 C5 10 2 7 1 3 C0.8 2 1.2 1 2 1 Z" fill="#555"/></svg><span>1-555-0142-3318</span></li>
      <li><svg width="13" height="10" viewBox="0 0 13 10"><rect x="0.5" y="0.5" width="12" height="9" fill="none" stroke="#555"/><path d="M0.5 0.5 L6.5 5.5 L12.5 0.5" fill="none" stroke="#555"/></svg><span>hello@velomarque-example.com</span></li>
    </ul>
  </div>
  <div class="footer-col links">
    <h4>QUICK LINKS</h4>
    <ul><li>HOME</li><li>ABOUT</li><li>BLOG</li><li>APP REVIEWS</li><li>VIDEOS</li><li>CONTACT</li></ul>
    <div class="footer-social"><span></span><span></span><span></span></div>
  </div>
  <div class="footer-rule"></div>
  <p class="copyright">Copyrights © 2017 Velomarque . Allrights Reserved.</p>
</footer>

</body>
</html>
```